Premium small-production winery needs a front label redesign

We produce wine from cold-climate varietal grapes, many of which were only developed in the last 50 years. Our winery, called Hollow Birch Cellars, is housed in an industrial style building serving a premium product. We have 12 styles of wine that can accommodate a wide range of tastes. We would like to see designs that communicate old traditions (winemaking styles) blended with new ideas (newly developed grape varieties). Our ideal customer enjoys an evening that is cultured and classy, yet fun and educational. We will likely favor designs that are 4" x 4.5", but this isn't required - if we see something we love, we would consider changing the dimensions.
I've attached our current labels and 2 logo files. We are only looking for a front-label redesign. Thanks!

Target Market(s)

Our ideal customer enjoys an evening that is cultured and classy, yet fun and educational.

Font styles to use
Serif
Sans Serif
Script
Other font styles liked:
• Our current fonts are Trajan Pro, Tangerine, and Avenir.

Requirements
Must have
• We would love to see a design that could span our entire product line with only a subtle or minor change (such as printing color, or a picture) to distinguish between our 12 products. Emphasis on the part about the change should be subtle among labels.
• Some of the distinguishing characteristics of the wines:
• Color: white, orange, rosé (pink), light red, dark red
• Sweetness: dry, off-dry, semi-sweet, sweet, very sweet
• Flavors: too many to list
• Product names: 9 of the wines are named after the majority grape. The other 3 are blends of multiple grapes, with the following names: "Velour Blush", "Opal", and "Ember".
Nice to have
• our wine list: http://hollowbirchcellars-example.com/wine/
Should not have
• We would prefer a design that isn't too busy overall.

```html
<!DOCTYPE html>
<html lang="en">
<head>
<meta charset="utf-8">
<title>Hollow Birch Cellars – Maréchal Foch front label</title>
<link href="https://fonts.googleapis.com/css2?family=Cinzel:wght@400&family=Pinyon+Script&display=swap" rel="stylesheet">
<style>
  :root {
    --page: #000000;
    --wine-glow: #f00a0a;
    --wine-mid: #a20f14;
    --wine-deep: #3a1016;
    --corner-red: #ff0a0a;
    --rule-red: #e8331a;
    --plaque-dark: #2a0d10;
    --ornament: #1c0a0c;
    --ink: #ffffff;
  }
  * { margin: 0; padding: 0; box-sizing: border-box; }
  html, body {
    width: 1092px; height: 1200px; overflow: hidden;
    background: var(--page);
  }
  .canvas { position: relative; width: 1092px; height: 1200px; }
  .label {
    position: absolute; left: 110px; top: 110px;
    width: 872px; height: 980px;
    background: radial-gradient(ellipse 70% 62% at 62% 51%, var(--wine-glow) 0%, var(--wine-mid) 38%, var(--wine-deep) 100%);
    overflow: hidden;
  }
  .label-art { position: absolute; inset: 0; }
  .brand-mark {
    position: absolute; left: 266px; top: 140px;
    width: 340px; height: 340px;
    display: flex; align-items: center; justify-content: center;
    text-align: center; color: var(--ink);
    font-family: "Cinzel", serif; font-weight: 400;
    font-size: 30px; line-height: 1.3; letter-spacing: 0.5px;
  }
  .winery-name {
    position: absolute; left: 0; right: 0; top: 524px;
    text-align: center; color: var(--ink);
    font-family: "Cinzel", serif; font-weight: 400;
    font-size: 58px; line-height: 80px;
  }
  .varietal {
    position: absolute; left: 218px; width: 436px; top: 718px; height: 120px;
    display: flex; align-items: center; justify-content: center;
    color: var(--ink);
    font-family: "Pinyon Script", cursive;
    font-size: 64px; line-height: 1;
  }
</style>
</head>
<body>
<main class="canvas">
  <section class="label">
    <svg class="label-art" width="872" height="980" viewBox="0 0 872 980">
      <defs>
        <radialGradient id="plaqueFill" cx="50%" cy="62%" r="60%">
          <stop offset="0%" stop-color="#f00a0a"/>
          <stop offset="55%" stop-color="#6a0d12"/>
          <stop offset="100%" stop-color="#2a0d10"/>
        </radialGradient>
      </defs>
      <g class="corner-tabs" fill="var(--corner-red)">
        <path d="M0 0 H44 A44 44 0 0 1 0 44 Z"/>
        <path d="M872 0 H828 A44 44 0 0 0 872 44 Z"/>
        <path d="M0 980 H44 A44 44 0 0 0 0 936 Z"/>
        <path d="M872 980 H828 A44 44 0 0 1 872 936 Z"/>
      </g>
      <path class="frame-rule" fill="none" stroke="var(--rule-red)" stroke-width="1.2"
        d="M74 20 H798 A56 56 0 0 0 854 76 V904 A56 56 0 0 0 798 960 H74 A56 56 0 0 0 18 904 V76 A56 56 0 0 0 74 20 Z"/>
      <circle class="brand-seal" cx="436" cy="310" r="170" fill="none" stroke="var(--ink)" stroke-width="3"/>
      <path role="img" aria-label="Scrollwork flourish to the left of the varietal plaque"
        d="M130 718 H234 V834 H130 Q110 776 130 718 Z" fill="var(--ornament)"/>
      <path role="img" aria-label="Scrollwork flourish to the right of the varietal plaque"
        d="M638 718 H742 Q762 776 742 834 H638 Z" fill="var(--ornament)"/>
      <rect class="plaque-shadow" x="234" y="702" width="404" height="152" fill="var(--plaque-dark)"/>
      <path class="plaque-body" fill="url(#plaqueFill)" stroke="var(--rule-red)" stroke-width="2"
        d="M248 714 H624 Q624 730 640 730 V824 Q624 824 624 840 H248 Q248 824 232 824 V730 Q248 730 248 714 Z"/>
    </svg>

    <div class="brand-mark">Hollow Birch<br>Cellars</div>

    <h1 class="winery-name">HOLLOW BIRCH<br>CELLARS</h1>

    <p class="varietal">Maréchal Foch</p>
  </section>
</main>
</body>
</html>
```